Business Card Design

Company is a Commercial Building Company specialising in New Construction and existing refurbishments

Industry/Entity Type

Business

Contact Information for Business Card

Liam Porter
Construction Manager
E Liam@marshbuilding.com.au
M 0400 213 594
Mail 14 Tarrant Rise Dawesville WA 6211

```html
<!DOCTYPE html>
<html lang="en">
<head>
<meta charset="utf-8">
<title>Marsh Building &amp; Construction – Business Card</title>
<link rel="stylesheet" href="https://fonts.googleapis.com/css2?family=Questrial&family=Didact+Gothic&display=swap">
<style>
  :root {
    --page: #e9e9e7;
    --card-white: #ffffff;
    --orange-top: #f7a12a;
    --orange-bottom: #f27b1c;
    --teal: #1fb3cf;
    --ink: #2e3138;
    --white: #ffffff;
  }
  * { margin: 0; padding: 0; box-sizing: border-box; }
  html, body {
    width: 1200px;
    height: 857px;
    overflow: hidden;
    background: var(--page);
  }
  .canvas {
    position: relative;
    width: 1200px;
    height: 857px;
    display: flex;
    align-items: center;
    justify-content: center;
    gap: 60px;
  }
  .card {
    width: 520px;
    height: 297px;
    border-radius: 28px;
    box-shadow: 0 6px 18px rgba(0, 0, 0, 0.12);
    display: flex;
    flex-direction: column;
    align-items: center;
    justify-content: center;
    text-align: center;
    font-family: "Questrial", sans-serif;
  }

  /* Front */
  .card-front { background: var(--card-white); }
  .brand-name {
    display: flex;
    flex-direction: column;
    align-items: center;
    gap: 2px;
    font-family: "Questrial", sans-serif;
    font-weight: 400;
    text-transform: uppercase;
    line-height: 1.05;
  }
  .card-front .brand-name { color: var(--ink); font-size: 26px; letter-spacing: 0.5px; }
  .brand-name .line-2 { font-size: 0.78em; }
  .holder-name {
    margin-top: 22px;
    color: var(--teal);
    font-family: "Didact Gothic", sans-serif;
    font-size: 17px;
    font-weight: 700;
    letter-spacing: 1px;
    text-transform: uppercase;
  }
  .holder-role {
    margin-top: 4px;
    color: var(--ink);
    font-size: 17px;
  }

  /* Back */
  .card-back {
    background: linear-gradient(160deg, var(--orange-top), var(--orange-bottom));
    justify-content: flex-start;
    padding-top: 92px;
  }
  .card-back .brand-name { color: var(--white); font-size: 24px; letter-spacing: 0.5px; }
  .contact {
    margin-top: auto;
    margin-bottom: 38px;
    color: var(--white);
    font-size: 14px;
    line-height: 1.45;
  }
  .contact-address { text-transform: uppercase; letter-spacing: 0.6px; }
  .contact-lines {
    display: flex;
    align-items: center;
    justify-content: center;
    gap: 6px;
    font-weight: 700;
  }
  .contact-item { display: inline-flex; align-items: center; gap: 4px; }
  .contact-item svg { width: 9px; height: 9px; }
</style>
</head>
<body>
<main class="canvas">
  <section class="card card-front" aria-label="Business card front">
    <div class="brand-name">
      <span class="line-1">Marsh Building</span>
      <span class="line-2">&amp; Construction</span>
    </div>
    <p class="holder-name">Liam Porter</p>
    <p class="holder-role">Construction Manager</p>
  </section>

  <section class="card card-back" aria-label="Business card back">
    <div class="brand-name">
      <span class="line-1">Marsh Building</span>
      <span class="line-2">&amp; Construction</span>
    </div>
    <div class="contact">
      <p class="contact-address">14 Tarrant Rise Dawesville WA 6211</p>
      <p class="contact-lines">
        <span class="contact-item">
          <svg viewBox="0 0 10 10" aria-hidden="true"><circle cx="5" cy="5" r="5" fill="#1fb3cf"/></svg>
          Liam@marshbuilding.com.au
        </span>
        <span class="contact-item">
          <svg viewBox="0 0 10 10" aria-hidden="true"><circle cx="5" cy="5" r="5" fill="#1fb3cf"/></svg>
          0400 213 594
        </span>
      </p>
    </div>
  </section>
</main>
</body>
</html>
```